Maple Grove Schools | brand new stationery!

We need stationery design with our new logo! Our company updated it's name and image and we like to incorporate the new one on our stationery, business cards and email signature. We are looking for fresh, new ideas!
Industry: Childcare, Elementary and Middle School
Company Name: Maple Grove Schools
Tagline: Bright Futures Start Here
Main colors: Blue, white and a little yellow
Star shape is something new for us! Do you see a way to incorporate it as a design element?

```html
<!DOCTYPE html>
<html lang="en">
<head>
<meta charset="utf-8">
<title>Maple Grove Schools – Business Card</title>
<link href="https://fonts.googleapis.com/css2?family=Poppins:wght@400;500;600;700&display=swap" rel="stylesheet">
<style>
  :root {
    --backdrop: #d4d4d4;
    --navy: #0b1f72;
    --ink: #1f1f1f;
    --paper: #ffffff;
    --charcoal: #1f1d1d;
    --gold: #f7b90f;
    --muted: #333333;
  }
  * { box-sizing: border-box; margin: 0; padding: 0; }
  html, body {
    width: 1200px; height: 807px; overflow: hidden;
    background: var(--backdrop);
    font-family: "Poppins", sans-serif;
  }
  .sheet {
    width: 1200px; height: 807px;
    display: flex; align-items: center; justify-content: center; gap: 40px;
  }
  .card {
    width: 540px; height: 309px; position: relative; overflow: hidden;
  }
  /* Front */
  .card--front {
    background: var(--paper);
    border: 2px solid var(--navy);
    padding: 30px 30px;
  }
  .brand-name {
    font-weight: 700; color: var(--ink);
    font-size: 34px; line-height: 1.0; letter-spacing: -0.5px;
  }
  .contact { margin-top: 16px; }
  .person-name {
    font-weight: 700; color: var(--navy);
    font-size: 19px; text-transform: uppercase; line-height: 1.1;
  }
  .person-role { font-size: 12px; color: var(--muted); margin-bottom: 8px; }
  .contact-list { list-style: none; font-size: 11.5px; color: var(--muted); line-height: 1.6; }
  .contact-list li { display: flex; align-items: center; gap: 8px; }
  .contact-list svg { width: 11px; height: 11px; fill: var(--navy); flex: none; }
  .address { margin-top: 8px; font-size: 11.5px; color: var(--muted); line-height: 1.5; }
  .mark-dot {
    position: absolute; right: 40px; top: 40px;
    width: 190px; height: 190px; border-radius: 50%;
    background: var(--navy);
  }
  /* Back */
  .card--back {
    background: var(--charcoal);
    display: flex; flex-direction: column; align-items: center; justify-content: center;
    text-align: center;
  }
  .back-dot {
    width: 54px; height: 54px; border-radius: 50%;
    background: var(--navy); margin-bottom: 14px;
  }
  .card--back .brand-name { color: var(--paper); font-size: 38px; }
  .tagline { margin-top: 18px; color: var(--gold); font-size: 22px; font-weight: 400; }
</style>
</head>
<body>
<main class="sheet">
  <section class="card card--front">
    <h1 class="brand-name">Maple Grove<br>Schools</h1>
    <div class="contact">
      <p class="person-name">Daniel Hayes</p>
      <p class="person-role">Managing Director</p>
      <ul class="contact-list">
        <li><svg viewBox="0 0 24 24"><path d="M6.6 10.8a15.1 15.1 0 0 0 6.6 6.6l2.2-2.2a1 1 0 0 1 1-.25 11.4 11.4 0 0 0 3.6.57 1 1 0 0 1 1 1V20a1 1 0 0 1-1 1A17 17 0 0 1 3 4a1 1 0 0 1 1-1h3.5a1 1 0 0 1 1 1c0 1.25.2 2.45.57 3.57a1 1 0 0 1-.25 1z"/></svg>044-555 010 222</li>
        <li><svg viewBox="0 0 24 24"><path d="M2 5h20v14H2zm2 2v.5l8 5 8-5V7l-8 5z"/></svg>hello@maplegrove.edu</li>
        <li><svg viewBox="0 0 24 24"><circle cx="12" cy="12" r="10"/></svg>www.maplegrove.edu</li>
      </ul>
      <p class="address">18 Orchard Lane<br>Springfield, 40210</p>
    </div>
    <div class="mark-dot" aria-hidden="true"></div>
  </section>

  <section class="card card--back">
    <div class="back-dot" aria-hidden="true"></div>
    <h2 class="brand-name">Maple Grove<br>Schools</h2>
    <p class="tagline">Bright Futures Start Here</p>
  </section>
</main>
</body>
</html>
```